Sales presentation introduction for Finance and Tech firms

Our business is two fold - 1) recruitment 2) consultancy. We would like a one or two page template that we can use to send to potential clients. The template will ideally be the same for the recruitment and consultancy side. We need to be able to edit the template to enter text.

I have attached our logo so you can see what we currently use on Corvella.

Sector is financial services and technology. We do not intent to have lots of text but the layout/images/designs to be used should cover some of page in a way that it takes up some space to avoid having to write lot of text.

Open to colour suggestions.

Please look at the attached word doc to see the text I would like for the two presentations.

Happy to answer questions.

Target Market(s)

Directors

Industry/Entity Type

Finance and tech companies

Colors
0094D4
00A9DD
6FCCEA
C7EBF8
E9F6FB

Requirements
Must have
• Editable text

```html
<!DOCTYPE html>
<html lang="en">
<head>
<meta charset="utf-8">
<title>Veltara Consultancy – Flyer</title>
<link rel="stylesheet" href="https://fonts.googleapis.com/css2?family=Montserrat:wght@400;500;600;800&display=swap">
<style>
  :root {
    --canvas: #e6e7ec;
    --paper: #f5f4fb;
    --blue: #1b79c4;
    --blue-deep: #1a56a8;
    --blue-sky: #6fb8ea;
    --ink: #1c1d22;
    --grey-text: #6d6e72;
    --footer: #58595b;
    --white: #ffffff;
  }
  * { margin: 0; padding: 0; box-sizing: border-box; }
  html, body { width: 1200px; height: 800px; overflow: hidden; }
  body { background: var(--canvas); font-family: "Montserrat", sans-serif; }
  .flyer {
    position: absolute; left: 324px; top: 10px;
    width: 552px; height: 780px;
    background: var(--paper);
    box-shadow: 0 2px 10px rgba(0,0,0,.12);
    overflow: hidden;
  }
  .flyer-shapes { position: absolute; inset: 0; }
  .brand {
    position: absolute; left: 26px; top: 190px;
    display: flex; align-items: center; gap: 10px;
  }
  .brand-mark { width: 20px; height: 20px; background: var(--blue); }
  .brand-name {
    font-weight: 400; font-size: 26px; line-height: 32px; letter-spacing: 1px;
    color: var(--grey-text);
  }
  .headline {
    position: absolute; left: 28px; top: 290px;
    font-weight: 800; font-size: 15px; line-height: 20px;
    color: var(--white);
  }
  .intro { position: absolute; left: 28px; top: 452px; width: 350px; }
  .intro-title { font-weight: 800; font-size: 17px; color: var(--ink); margin-bottom: 6px; }
  .intro p { font-size: 9px; line-height: 12.5px; color: var(--ink); margin-bottom: 5px; }
  .service {
    position: absolute; display: flex; align-items: center; gap: 8px;
    width: 160px;
  }
  .service-icon { width: 40px; height: 40px; flex: none; }
  .service-label { font-size: 9.5px; line-height: 11.5px; font-weight: 500; color: var(--ink); }
  .contact-bar {
    position: absolute; left: 0; bottom: 0; width: 100%; height: 46px;
    background: var(--footer);
    display: flex; align-items: center; justify-content: space-around;
    padding: 0 16px;
  }
  .contact-item { display: flex; align-items: center; gap: 7px; color: var(--white); font-size: 10.5px; font-weight: 500; }
  .contact-icon { width: 18px; height: 18px; }
</style>
</head>
<body>
<main class="flyer">
  <svg class="flyer-shapes" viewBox="0 0 552 780" width="552" height="780">
    <defs>
      <linearGradient id="skyline-tone" x1="0" y1="0" x2="1" y2="1">
        <stop offset="0" stop-color="#d5ddec"/>
        <stop offset="0.5" stop-color="#9db1d3"/>
        <stop offset="1" stop-color="#4d6fa6"/>
      </linearGradient>
    </defs>
    <polygon points="0,0 552,0 552,230 400,350 0,10" fill="url(#skyline-tone)" role="img" aria-label="Photograph looking up at glass office towers against a pale sky"/>
    <polygon points="0,10 400,350 400,362 0,22" fill="var(--blue-deep)"/>
    <polygon points="400,350 552,230 552,250 412,362" fill="var(--blue-deep)"/>
    <polygon points="424,364 552,262 552,330" fill="var(--blue-sky)"/>
    <polygon points="0,232 330,310 330,442 0,442" fill="var(--blue)"/>
  </svg>

  <div class="brand">
    <span class="brand-mark"></span>
    <span class="brand-name">VELTARA</span>
  </div>

  <h1 class="headline">A partner who brings<br>new and innovative<br>ideas to the table,<br>through extensive industry<br>experience and knowledge.<br>Veltara will ensure you are<br>prepared for growth.</h1>

  <section class="intro">
    <h2 class="intro-title">Veltara Consultancy</h2>
    <p>Veltara E2E is a bespoke consultancy firm that specialises in buy side investment. Through an industry based consultative approach we assist our clients in preparing for, and facilitating, long term growth. Working closely with our clients we combine innovative thinking and breakthrough technologies to accelerate progress and, together, achieve enduring results.</p>
    <p>Experienced in successfully delivering change for global organisations as well as assisting smaller firms during their growth phase. Veltara will work with you create a workable model and ensure</p>
  </section>

  <div class="service" style="left:390px; top:452px;">
    <svg class="service-icon" viewBox="0 0 40 40"><circle cx="20" cy="20" r="20" fill="var(--blue-deep)"/><rect x="13" y="10" width="14" height="19" rx="1" fill="none" stroke="#fff" stroke-width="1.5"/><path d="M16 16h8M16 20h8M16 24h5" stroke="#fff" stroke-width="1.3"/><path d="M22 27l2 2 4-5" fill="none" stroke="#fff" stroke-width="1.5"/></svg>
    <span class="service-label">Compliance</span>
  </div>
  <div class="service" style="left:390px; top:498px;">
    <svg class="service-icon" viewBox="0 0 40 40"><circle cx="20" cy="20" r="20" fill="var(--blue-deep)"/><rect x="12" y="11" width="16" height="18" rx="1" fill="none" stroke="#fff" stroke-width="1.5"/><path d="M15 25v-4M19 25v-7M23 25v-10" stroke="#fff" stroke-width="2"/></svg>
    <span class="service-label">Finance<br>and<br>Accounting</span>
  </div>
  <div class="service" style="left:390px; top:544px;">
    <svg class="service-icon" viewBox="0 0 40 40"><circle cx="20" cy="20" r="20" fill="var(--blue-deep)"/><rect x="11" y="15" width="18" height="13" rx="1" fill="none" stroke="#fff" stroke-width="1.5"/><path d="M17 15v-3h6v3M11 20h18" stroke="#fff" stroke-width="1.5" fill="none"/></svg>
    <span class="service-label">Middle<br>and<br>Back Office</span>
  </div>

  <div class="service" style="left:210px; top:600px;">
    <svg class="service-icon" viewBox="0 0 40 40"><circle cx="20" cy="20" r="20" fill="var(--blue-deep)"/><circle cx="16" cy="16" r="3.5" fill="none" stroke="#fff" stroke-width="1.5"/><path d="M10 28c0-4 3-7 6-7s6 3 6 7" fill="none" stroke="#fff" stroke-width="1.5"/><path d="M24 13h6M24 17h6M24 21h4" stroke="#fff" stroke-width="1.3"/></svg>
    <span class="service-label">CRM/<br>Onboarding</span>
  </div>
  <div class="service" style="left:210px; top:644px;">
    <svg class="service-icon" viewBox="0 0 40 40"><circle cx="20" cy="20" r="20" fill="var(--blue-deep)"/><circle cx="20" cy="20" r="8" fill="none" stroke="#fff" stroke-width="1.5"/><path d="M20 12v8h8" fill="none" stroke="#fff" stroke-width="1.5"/></svg>
    <span class="service-label">Performance,<br>Risk and<br>Attribution</span>
  </div>
  <div class="service" style="left:210px; top:688px;">
    <svg class="service-icon" viewBox="0 0 40 40"><circle cx="20" cy="20" r="20" fill="var(--blue-deep)"/><rect x="11" y="11" width="14" height="18" rx="1" fill="none" stroke="#fff" stroke-width="1.5"/><circle cx="25" cy="22" r="4" fill="var(--blue-deep)" stroke="#fff" stroke-width="1.5"/><path d="M28 25l3 3" stroke="#fff" stroke-width="1.8"/></svg>
    <span class="service-label">Client and<br>Regulatory<br>Reporting</span>
  </div>

  <div class="service" style="left:28px; top:600px;">
    <svg class="service-icon" viewBox="0 0 40 40"><circle cx="20" cy="20" r="20" fill="var(--blue-deep)"/><rect x="13" y="10" width="15" height="19" rx="1" fill="none" stroke="#fff" stroke-width="1.5"/><circle cx="16" cy="25" r="4" fill="var(--blue-deep)" stroke="#fff" stroke-width="1.5"/><path d="M19 15h6M19 19h6" stroke="#fff" stroke-width="1.3"/></svg>
    <span class="service-label">Order<br>Management<br>and Trading</span>
  </div>
  <div class="service" style="left:28px; top:644px;">
    <svg class="service-icon" viewBox="0 0 40 40"><circle cx="20" cy="20" r="20" fill="var(--blue-deep)"/><path d="M12 28v-4M16 28v-7M20 28v-5M24 28v-9" stroke="#fff" stroke-width="2"/><path d="M11 20l6-5 4 3 8-7" fill="none" stroke="#fff" stroke-width="1.5"/></svg>
    <span class="service-label">Investment<br>and<br>Research</span>
  </div>
  <div class="service" style="left:28px; top:688px;">
    <svg class="service-icon" viewBox="0 0 40 40"><circle cx="20" cy="20" r="20" fill="var(--blue-deep)"/><circle cx="18" cy="18" r="6" fill="none" stroke="#fff" stroke-width="1.5"/><path d="M22.5 22.5l6 6" stroke="#fff" stroke-width="2"/></svg>
    <span class="service-label">Investment<br>and<br>Research</span>
  </div>

  <footer class="contact-bar">
    <span class="contact-item">
      <svg class="contact-icon" viewBox="0 0 18 18"><circle cx="9" cy="9" r="8.3" fill="none" stroke="#fff" stroke-width="1"/><path d="M6 5l1.6-.4 1 2.2-1 .8c.5 1.1 1.3 1.9 2.4 2.4l.8-1 2.2 1-.4 1.6c-3.5 0-6.6-3.1-6.6-6.6z" fill="#fff"/></svg>
      +44 (0) 7700 900412
    </span>
    <span class="contact-item">
      <svg class="contact-icon" viewBox="0 0 18 18"><circle cx="9" cy="9" r="8.3" fill="none" stroke="#fff" stroke-width="1"/><rect x="5" y="6" width="8" height="6" fill="none" stroke="#fff" stroke-width="1"/><path d="M5 6l4 3.2L13 6" fill="none" stroke="#fff" stroke-width="1"/></svg>
      info@veltara-e2e.com
    </span>
    <span class="contact-item">
      <svg class="contact-icon" viewBox="0 0 18 18"><circle cx="9" cy="9" r="8.3" fill="none" stroke="#fff" stroke-width="1"/><circle cx="9" cy="9" r="4.5" fill="none" stroke="#fff" stroke-width="1"/><path d="M4.5 9h9M9 4.5c-2 2.5-2 6.5 0 9M9 4.5c2 2.5 2 6.5 0 9" fill="none" stroke="#fff" stroke-width=".8"/></svg>
      www.veltara-e2e.com
    </span>
  </footer>
</main>
</body>
</html>
```